FinTech company looking to revamp and expand client-facing interface for our financial models

Pellworth Engines currently has a very simple website that allows clients to interact with our financial models. We are looking to completely redesign the current site and add several extra pages to provide extra functionality. We want the design to have a modern, slick feel, that will work on both a desktop or a tablet. It should be straightforward for clients to move between different pages at any time, and clear from the layout how to interact with the more advanced features. We have included screenshots of existing pages in the attached design brief, as well as sketches of the functionality required by the new pages, but can't provide a direct link to the current site.
Target Market(s)
Professional investors that will be paying to access the interface
Industry/Entity Type
Finance
Number of Pages Required
4 page
Colors
Designer to choose colors to be used in the design.
Look and feel
Each slider illustrates characteristics of the customer's brand and the style your logo design should communicate.

```html
<!DOCTYPE html>
<html lang="en">
<head>
<meta charset="utf-8">
<title>Pellworth Engines – Models &amp; Sensitivities</title>
<link href="https://fonts.googleapis.com/css2?family=Lato:wght@400;700&display=swap" rel="stylesheet">
<style>
  :root{
    --backdrop:#6d6b6b;
    --bar:#333333;
    --page:#f6f6f6;
    --white:#ffffff;
    --ink:#2b2b2b;
    --muted:#e6e6e6;
    --accent:#f2a900;
    --green:#3a9a1e;
    --line:#d6d6d6;
    --stripe:#f5f5f5;
  }
  *{box-sizing:border-box;margin:0;padding:0}
  html,body{width:1200px;height:941px;overflow:hidden}
  body{background:var(--backdrop);font-family:'Lato',sans-serif;color:var(--ink);position:relative}
  .screen{position:absolute;left:129px;width:956px;background:var(--page)}
  .screen--models{top:48px;height:397px}
  .screen--sens{top:483px;height:418px}
  .topbar{height:42px;background:var(--bar);display:flex;align-items:center;padding:0 24px 0 22px}
  .brand{color:var(--white);font-weight:700;font-size:14px;letter-spacing:.1px;margin-right:22px}
  .counts{display:flex;gap:15px;color:var(--white);font-size:8.5px;font-weight:700}
  .nav{margin-left:auto;display:flex;gap:20px}
  .nav a{color:var(--muted);text-decoration:none;font-size:8px;font-weight:700;letter-spacing:.3px;display:flex;align-items:center;gap:4px}
  .nav a.is-active{color:var(--accent)}
  .nav svg{width:8px;height:8px}
  .filters{position:absolute;left:21px}
  .field{display:flex;align-items:center;height:23px;margin-bottom:6px}
  .field label{width:92px;font-size:8.3px;font-weight:700}
  .field input{width:151px;height:23px;border:1px solid var(--line);background:var(--white);font:700 8.3px 'Lato',sans-serif;color:var(--ink);padding-left:6px}
  .export{position:absolute;left:21px;display:flex;align-items:center;gap:4px;color:var(--green);font-size:8.3px;font-weight:700;text-decoration:none}
  .export svg{width:11px;height:10px}
  .grid{position:absolute;left:21px;width:910px;border:1px solid var(--line);border-collapse:collapse;table-layout:fixed;background:var(--white);font-size:8.3px;font-weight:700}
  .grid th,.grid td{text-align:left;padding-left:10px;white-space:nowrap}
  .grid thead tr{height:34px;background:linear-gradient(#fbfbfb,#f1f1f1);border-bottom:1px solid var(--line)}
  .grid th{font-weight:700}
  .grid th.sortable{color:var(--green)}
  .grid tbody tr{height:38px}
  .grid tbody tr:nth-child(even){background:var(--stripe)}
  .caret{display:inline-block;width:0;height:0;border-left:3px solid transparent;border-right:3px solid transparent;border-top:3px solid var(--green);margin-left:4px;vertical-align:middle}
  .shift-sector{padding-left:32px !important}
</style>
</head>
<body>

<section class="screen screen--models">
  <header class="topbar">
    <span class="brand">Pellworth Engines</span>
    <div class="counts"><span>2500</span><span>830</span><span>420</span></div>
    <nav class="nav">
      <a class="is-active" href="#"><svg viewBox="0 0 10 10"><path d="M5 1 0.5 5H2v4h2.3V6.5h1.4V9H8V5h1.5z" fill="currentColor"/></svg>MODELS</a>
      <a href="#"><svg viewBox="0 0 10 10"><circle cx="5" cy="5" r="3.3" fill="none" stroke="currentColor" stroke-width="1.2" stroke-dasharray="1.6 .8"/></svg>SENSITIVITIES</a>
      <a href="#"><svg viewBox="0 0 10 10"><path d="M5 .5 6.3 3.6 9.6 3.8 7.1 6 7.9 9.3 5 7.5 2.1 9.3 2.9 6 .4 3.8 3.7 3.6z" fill="currentColor"/></svg>FAVOURITES</a>
    </nav>
  </header>

  <form class="filters" style="top:57px">
    <div class="field"><label>Quality Threshold:</label><input value="-10"></div>
    <div class="field"><label>Abs. Stat Threshold:</label><input value="-10"></div>
  </form>

  <a class="export" href="#" style="top:123px"><svg viewBox="0 0 12 11"><path d="M1 3h4M1 3v7h8V7" fill="none" stroke="currentColor" stroke-width="1.3"/><path d="M4 7c0-3 2-4 5-4V1l3 3-3 3V5C7 5 5 5.5 4 7z" fill="currentColor"/></svg>Export</a>

  <table class="grid" style="top:149px">
    <colgroup><col style="width:57px"><col style="width:129px"><col style="width:151px"><col style="width:64px"><col style="width:65px"><col style="width:64px"><col style="width:65px"><col style="width:64px"><col style="width:65px"><col style="width:64px"><col style="width:65px"><col style="width:57px"></colgroup>
    <thead><tr><th class="sortable">ID<span class="caret"></span></th><th class="sortable">Sector</th><th class="sortable">Time</th><th>Quality</th><th>Stat 1</th><th>Stat 2</th><th>Stat 3</th><th>Stat 4</th><th>Stat 5</th><th>Stat 6</th><th>Stat 7</th><th>Stat 8</th></tr></thead>
    <tbody>
      <tr><td>Model 1</td><td>Materials</td><td>2019-07-03 / 12:15:00.000</td><td>30.2288</td><td>2.01574</td><td>23.305</td><td>-0.149368</td><td>22.3054</td><td>4.63714</td><td>0.945706</td><td>2.81949</td><td>2.60858</td></tr>
      <tr><td>Model 2</td><td>Industrials</td><td>2019-07-03 / 12:15:00.000</td><td>30.2288</td><td>2.01574</td><td>23.305</td><td>-0.149368</td><td>22.3054</td><td>4.63714</td><td>0.945706</td><td>2.81949</td><td>2.60858</td></tr>
      <tr><td>Model 3</td><td>Consumer Discretionary</td><td>2019-07-03 / 12:15:00.000</td><td>30.2288</td><td>2.01574</td><td>23.305</td><td>-0.149368</td><td>22.3054</td><td>4.63714</td><td>0.945706</td><td>2.81949</td><td>2.60858</td></tr>
      <tr><td>Model 4</td><td>Information Technology</td><td>2019-07-03 / 12:15:00.000</td><td>30.2288</td><td>2.01574</td><td>23.305</td><td>-0.149368</td><td>22.3054</td><td>4.63714</td><td>0.945706</td><td>2.81949</td><td>2.60858</td></tr>
      <tr><td>Model 5</td><td>Information Technology</td><td>2019-07-03 / 12:15:00.000</td><td>30.2288</td><td>2.01574</td><td>23.305</td><td>-0.149368</td><td>22.3054</td><td>4.63714</td><td>0.945706</td><td>2.81949</td><td>2.60858</td></tr>
    </tbody>
  </table>
</section>

<section class="screen screen--sens">
  <header class="topbar">
    <span class="brand">Pellworth Engines</span>
    <div class="counts"><span>2500</span><span>830</span><span>420</span></div>
    <nav class="nav">
      <a href="#"><svg viewBox="0 0 10 10"><path d="M5 1 0.5 5H2v4h2.3V6.5h1.4V9H8V5h1.5z" fill="currentColor"/></svg>MODELS</a>
      <a class="is-active" href="#"><svg viewBox="0 0 10 10"><circle cx="5" cy="5" r="3.3" fill="none" stroke="currentColor" stroke-width="1.2" stroke-dasharray="1.6 .8"/></svg>SENSITIVITIES</a>
      <a href="#"><svg viewBox="0 0 10 10"><path d="M5 .5 6.3 3.6 9.6 3.8 7.1 6 7.9 9.3 5 7.5 2.1 9.3 2.9 6 .4 3.8 3.7 3.6z" fill="currentColor"/></svg>FAVOURITES</a>
    </nav>
  </header>

  <form class="filters" style="top:57px">
    <div class="field"><label>Stat 1 Threshold:</label><input value="-10"></div>
    <div class="field"><label>Stat 2 Threshold:</label><input value="-10"></div>
    <div class="field"><label>Stat 2 Threshold:</label><input value="-10"></div>
  </form>

  <a class="export" href="#" style="top:153px"><svg viewBox="0 0 12 11"><path d="M1 3h4M1 3v7h8V7" fill="none" stroke="currentColor" stroke-width="1.3"/><path d="M4 7c0-3 2-4 5-4V1l3 3-3 3V5C7 5 5 5.5 4 7z" fill="currentColor"/></svg>Export</a>

  <table class="grid" style="top:173px">
    <colgroup><col style="width:57px"><col style="width:86px"><col style="width:86px"><col style="width:65px"><col style="width:64px"><col style="width:65px"><col style="width:64px"><col style="width:65px"><col style="width:358px"></colgroup>
    <thead><tr><th class="sortable">Factor<span class="caret"></span></th><th class="sortable">DI</th><th class="sortable shift-sector">Sector</th><th>Stat 1</th><th>Stat 2</th><th>Stat 3</th><th>Stat 4</th><th>Stat 5</th><th>Stat 6</th></tr></thead>
    <tbody>
      <tr><td>Factor 1</td><td>Model 1</td><td>Materials</td><td>-1.4</td><td>0.1</td><td>-3.1</td><td>0.7</td><td>30.2</td><td>0.9</td></tr>
      <tr><td>Factor 2</td><td>Model 2</td><td>Materials</td><td>-1.4</td><td>0.1</td><td>-3.1</td><td>0.7</td><td>30.2</td><td>0.9</td></tr>
      <tr><td>Factor 3</td><td>Model 3</td><td>Materials</td><td>-1.4</td><td>0.1</td><td>-3.1</td><td>0.7</td><td>30.2</td><td>0.9</td></tr>
      <tr><td>Factor 4</td><td>Model 4</td><td>Materials</td><td>-1.4</td><td>0.1</td><td>-3.1</td><td>0.7</td><td>30.2</td><td>0.9</td></tr>
      <tr><td>Factor 5</td><td>Model 5</td><td>Materials</td><td>-1.4</td><td>0.1</td><td>-3.1</td><td>0.7</td><td>30.2</td><td>0.9</td></tr>
    </tbody>
  </table>
</section>

</body>
</html>
```